HBG Business Cards

I need business cards for "harbor gate partners llc" doublesided... logo on the back (also include logo on front)
logo attached to project... i have jpg up.. let me know if you need eps file.
Company Info:
214 North Falcon Avenue, Suite 7B
Chicago, Illinois 60654
facsimile 312-448-2817 (list fax, address, website on all cards.)
www.harborgatepartnersllc.example
Three different people on cards:
Darius K. Feldt, CPA MST
Principal
ofc 312-448-2900
mobile 312-571-3348
dariuskfeldt@harborgatepartnersllc.example
Marcus T. Pelloway, CPA MST
Principal
marcustpelloway@harborgatepartnersllc.example
mobile 708-514-2297
ofc 312-448-2900
Owen B Tarrick
Principal
ofc 312-448-2900
no mobile
owenbtarrick@harborgatepartnersllc.example
I have multiple projects listed.. see below:
Business cards for harbor gate partners llc
letterhead
envelopes
Business cards for KV Merchant LLC
letterhead
envelopes
Target Market(s)
rich people
Industry/Entity Type
Business
Look and feel
Each slider illustrates characteristics of the customer's brand and the style your logo design should communicate.

```html
<!DOCTYPE html>
<html lang="en">
<head>
<meta charset="utf-8">
<title>Harbor Gate Partners LLC – Business Cards</title>
<link rel="stylesheet" href="https://fonts.googleapis.com/css2?family=Arimo:wght@400&display=swap">
<style>
  :root {
    --backdrop: #57585a;
    --card: #ffffff;
    --card-front: #f3f3f4;
    --navy: #1f3f78;
    --band: #6d6e70;
    --band-text: #ffffff;
  }
  * { box-sizing: border-box; margin: 0; padding: 0; }
  html, body {
    width: 1200px; height: 1000px; overflow: hidden;
    background: var(--backdrop);
    font-family: "Arimo", Arial, sans-serif;
  }
  .sheet { position: relative; width: 1200px; height: 1000px; }
  .card {
    position: absolute; width: 498px; height: 292px;
    background: var(--card); overflow: hidden;
  }
  .card--front { left: 77px; background: var(--card-front); }
  .card--back { left: 625px; }
  .row-1 { top: 31px; }
  .row-2 { top: 349px; }
  .row-3 { top: 666px; }

  .wordmark {
    display: flex; align-items: center; gap: 10px;
    color: var(--navy); text-transform: uppercase; white-space: nowrap;
    font-weight: 400;
  }
  .wordmark__dot { border-radius: 50%; background: var(--navy); flex: none; }

  .card--front .wordmark {
    position: absolute; left: 0; right: 0; top: 0; bottom: 0;
    justify-content: center; font-size: 27px; letter-spacing: 1px;
  }
  .card--front .wordmark__dot { width: 16px; height: 16px; }

  .card--back .wordmark {
    position: absolute; right: 34px; top: 94px;
    font-size: 14px; letter-spacing: 0.5px; gap: 7px;
  }
  .card--back .wordmark__dot { width: 9px; height: 9px; }

  .name-band {
    position: absolute; left: 0; top: 143px; width: 303px; height: 40px;
    background: var(--band); color: var(--band-text);
    padding: 3px 0 0 24px;
  }
  .name-band__name { font-size: 19px; line-height: 21px; }
  .name-band__title { font-size: 12px; line-height: 13px; }

  .contact {
    position: absolute; left: 24px; top: 190px;
    color: var(--navy); font-size: 11.5px; line-height: 15px;
  }
  .contact__group + .contact__group { margin-top: 5px; }
  .contact--short { top: 204px; }

  .footer-bar {
    position: absolute; left: 0; right: 0; bottom: 0; height: 14px;
    background: var(--band);
  }
</style>
</head>
<body>
<main class="sheet">

  <!-- Row 1 -->
  <section class="card card--front row-1">
    <div class="wordmark"><span class="wordmark__dot"></span>Harbor Gate Partners LLC</div>
  </section>
  <section class="card card--back row-1">
    <div class="wordmark"><span class="wordmark__dot"></span>Harbor Gate Partners LLC</div>
    <div class="name-band">
      <p class="name-band__name">Darius K. Feldt, CPA MST</p>
      <p class="name-band__title">Principal</p>
    </div>
    <div class="contact">
      <div class="contact__group">
        <p>Office : 312-448-2900</p>
        <p>Mobile : 312-571-3348</p>
        <p>Email : dariuskfeldt@harborgatepartnersllc.example</p>
      </div>
      <div class="contact__group">
        <p>Address : 214 North Falcon Avenue, Suite 7B Chicago, Illinois 60654</p>
        <p>Facsimile : 312-448-2817 | Web : www.harborgatepartnersllc.example</p>
      </div>
    </div>
    <div class="footer-bar"></div>
  </section>

  <!-- Row 2 -->
  <section class="card card--front row-2">
    <div class="wordmark"><span class="wordmark__dot"></span>Harbor Gate Partners LLC</div>
  </section>
  <section class="card card--back row-2">
    <div class="wordmark"><span class="wordmark__dot"></span>Harbor Gate Partners LLC</div>
    <div class="name-band">
      <p class="name-band__name">Marcus T. Pelloway, CPA MST</p>
      <p class="name-band__title">Principal</p>
    </div>
    <div class="contact">
      <div class="contact__group">
        <p>Office : 312-448-2900</p>
        <p>Mobile : 708-514-2297</p>
        <p>Email : marcustpelloway@harborgatepartnersllc.example</p>
      </div>
      <div class="contact__group">
        <p>Address : 214 North Falcon Avenue, Suite 7B Chicago, Illinois 60654</p>
        <p>Facsimile : 312-448-2817 | Web : www.harborgatepartnersllc.example</p>
      </div>
    </div>
    <div class="footer-bar"></div>
  </section>

  <!-- Row 3 -->
  <section class="card card--front row-3">
    <div class="wordmark"><span class="wordmark__dot"></span>Harbor Gate Partners LLC</div>
  </section>
  <section class="card card--back row-3">
    <div class="wordmark"><span class="wordmark__dot"></span>Harbor Gate Partners LLC</div>
    <div class="name-band">
      <p class="name-band__name">Owen B Tarrick</p>
      <p class="name-band__title">Principal</p>
    </div>
    <div class="contact contact--short">
      <div class="contact__group">
        <p>Office : 312-448-2900</p>
        <p>Email : owenbtarrick@harborgatepartnersllc.example</p>
      </div>
      <div class="contact__group">
        <p>Address : 214 North Falcon Avenue, Suite 7B Chicago, Illinois 60654</p>
        <p>Facsimile : 312-448-2817 | Web : www.harborgatepartnersllc.example</p>
      </div>
    </div>
    <div class="footer-bar"></div>
  </section>

</main>
</body>
</html>
```